Visitenkarten/Briefpaier/Kassenkassenbelege für Juwelier
Zielgruppe
Mittelständischer Juwelier mit zwei Filialen. Klassischer Schmuck, Uhren und Modeschmuck
Aufgabenstellung
Es müssen für zwei Geschäfte Visitenkarten, Briefpapier (A4) und Kassenkassenbelege (A6) erstellt werden. Logo und Typo im Anhang. Ein Farbkonzept besteht noch nicht. Die Idee geht in Richtung Bordeaux-Rot.
Generell:
(1) Sieht erstmal nach viel Beschreibung aus, bitte nicht entmutigen lassen, sind zu 90% nur austauschbare Inhalts-/Kontaktdaten.
(2) Für meine Zwecke reicht es vollkommen aus, wenn bei den Vorschlägen zur Arbeitsersparnis erstmal nur mit einer Adresse gearbeitet wird. Wenn ich dann den zutreffenden Designvorschlag gefunden habe, können wir die zweite Adresse in dem ersten Format umsetzen. Ich denke das spart Zeit und Nerven.
(3) Bitte Angaben wie "Tel.:" oder "USt.- ID:" nicht wörtlich nehmen, es soll dabei klar sein worum es geht; wenn "Telefon" ausgeschrieben besser aussieht, bitte in der optisch ansprechenderen Form verwenden.
(4) Bei Fragen, bitte fragen!
(5) Viel Spass bei dem Projekt - Ich freu' mich auf die Vorschläge!
Visitenkarten(1):
Juwelier Brenneck GmbH
www.juwelier-brenneck-beispiel.de
Visitenkarten(2):
Visitenkarten(generell):
(1) Die einzelnen Daten können durch Hervorhebungen wie Adresse, Kontakt, Online/Internet unterteilt bzw. hervorgehoben werden.
(2) Die Visitenkarten sollen farbig gedruckt werden; geplant ist weiß als Hintergrund ist aber nicht zwingend bei einer guten anderen Idee
Briefpapier:
(1)Absender im Adressfeld für DIN-lang Briefumschläge mit Fenster:
(2)Informationen im Footer/Seitenbereich:
Juwelier Brenneck Gmb..

```html
<!DOCTYPE html>
<html lang="de">
<head>
<meta charset="utf-8">
<title>Juwelier Brenneck – Briefpapier und Umschläge</title>
<link href="https://fonts.googleapis.com/css2?family=Source+Sans+3:wght@400;600;700&display=swap" rel="stylesheet">
<style>
  :root {
    --bg: #f7f7f7;
    --paper: #ffffff;
    --taupe: #847a6e;
    --teal: #023a4a;
    --mark: #555555;
    --window: #e2e2e2;
  }
  * { margin: 0; padding: 0; box-sizing: border-box; }
  html, body { width: 1200px; height: 1000px; overflow: hidden; background: var(--bg); }
  body { position: relative; font-family: "Source Sans 3", "Source Sans Pro", sans-serif; color: var(--taupe); }
  .sheet, .envelope { position: absolute; background: var(--paper); box-shadow: 1px 2px 4px rgba(0,0,0,.25); }

  /* Name line in the text font */
  .brand { position: absolute; display: flex; align-items: center; gap: 8px; }
  .brand-dot { width: 10px; height: 10px; border-radius: 50%; background: var(--taupe); flex: none; }
  .brand-name { font-size: 20px; font-weight: 600; color: var(--taupe); white-space: nowrap; }

  /* Letterhead */
  .letterhead { left: 42px; top: 50px; width: 533px; height: 753px; }
  .letterhead .brand { left: 34px; top: 70px; }

  .contact-box { position: absolute; left: 389px; top: 16px; width: 144px; height: 119px; background: var(--taupe);
    color: #fff; text-align: right; padding: 19px 12px 0 0; font-size: 7.4px; line-height: 10.8px; font-style: normal; }
  .contact-box .company { font-size: 9.2px; font-weight: 600; margin-bottom: 1px; }
  .contact-box .gap { height: 10.5px; }

  .fold-mark { position: absolute; left: 0; width: 19px; height: 1px; background: #d8d8d8; }

  .footer { position: absolute; left: 0; right: 0; top: 707px; border-top: 2px solid var(--taupe); height: 46px; font-size: 6.4px; line-height: 8.1px; }
  .footer-col { position: absolute; top: 7px; }
  .footer-col.bank { left: 65px; }
  .footer-col.tax { left: 246px; top: 11px; }
  .footer-col.branch { left: 412px; top: 11px; font-size: 7.2px; }
  .footer-divider { position: absolute; top: 4px; width: 1px; height: 29px; background: #d9d4ce; }

  .crop { position: absolute; background: var(--mark); }
  .crop.v { width: 1px; height: 25px; }
  .crop.h { width: 25px; height: 1px; }

  /* Envelope front */
  .envelope.front { left: 622px; top: 100px; width: 560px; height: 286px; border-bottom: 6px solid var(--taupe); }
  .sender { position: absolute; left: 35px; top: 25px; font-size: 7.4px; line-height: 10.8px; font-style: normal; }
  .sender .company { color: var(--teal); font-size: 9.2px; font-weight: 700; }
  .window { position: absolute; left: 39px; top: 153px; width: 223px; height: 89px; border-radius: 10px;
    border: 1px solid var(--window); box-shadow: inset 1px 2px 3px rgba(0,0,0,.18); }
  .envelope.front .brand { left: 376px; top: 196px; }

  /* Envelope back */
  .envelope.back { left: 622px; top: 475px; width: 560px; height: 285px; }
  .flap { position: absolute; left: 0; top: 0; }
  .envelope.back .brand { left: 50%; transform: translateX(-50%); top: 22px; }
  .envelope.back .brand-name { font-size: 14px; }
  .envelope.back .brand-dot { width: 8px; height: 8px; }
</style>
</head>
<body>

  <div class="crop v" style="left:42px;top:11px"></div>
  <div class="crop v" style="left:575px;top:11px"></div>
  <div class="crop v" style="left:42px;top:816px"></div>
  <div class="crop v" style="left:575px;top:816px"></div>
  <div class="crop h" style="left:5px;top:50px"></div>
  <div class="crop h" style="left:588px;top:50px"></div>
  <div class="crop h" style="left:5px;top:803px"></div>
  <div class="crop h" style="left:588px;top:803px"></div>

  <section class="sheet letterhead">
    <div class="brand">
      <span class="brand-dot"></span>
      <span class="brand-name">Juwelier Brenneck</span>
    </div>

    <address class="contact-box">
      <div class="company">Juwelier Brenneck GmbH</div>
      <div>Lindenallee 24</div>
      <div>45100 Auestadt a.d. Ruhr</div>
      <div class="gap"></div>
      <div>Tel.: 0201-000111</div>
      <div>Fax: 0201-000112</div>
      <div>info@juwelier-brenneck-beispiel.de</div>
      <div>www.juwelier-brenneck-beispiel.de</div>
    </address>

    <div class="fold-mark" style="top:268px"></div>
    <div class="fold-mark" style="top:520px"></div>

    <footer class="footer">
      <div class="footer-col bank">Bankverbindung:<br>Beispielbank AG Essen<br>IBAN: DE00 1234 5678 9012 3456 78<br>BIC: BSPL DE 1X</div>
      <div class="footer-divider" style="left:207px"></div>
      <div class="footer-col tax">Steuernummer:<br>100/2000/3000<br>USt.- ID: DE 000111222</div>
      <div class="footer-divider" style="left:349px"></div>
      <div class="footer-col branch">Filiale:<br>Kastanienweg 8<br>45500 Talheim</div>
    </footer>
  </section>

  <section class="envelope front">
    <address class="sender">
      <div class="company">Juwelier Brenneck GmbH</div>
      <div>Lindenallee 24</div>
      <div>45100 Auestadt a.d. Ruhr</div>
    </address>
    <div class="window"></div>
    <div class="brand">
      <span class="brand-dot"></span>
      <span class="brand-name">Juwelier Brenneck</span>
    </div>
  </section>

  <section class="envelope back">
    <svg class="flap" width="560" height="70" viewBox="0 0 560 70">
      <path d="M0 0 L32 58 Q37 63 52 63 L499 63 Q520 63 533 48 L560 4" fill="none" stroke="#dcdcdc" stroke-width="1.2"/>
    </svg>
    <div class="brand">
      <span class="brand-dot"></span>
      <span class="brand-name">Juwelier Brenneck</span>
    </div>
  </section>

</body>
</html>
```